Webdesign für Metallverarbeitung
Zielgruppe
Metallverarbeitung, Verpackung, Automobilzulieferer, Lasertechnik, Elektrotechnik, CAD Verarbeitung
Aufgabenstellung
-Farbe: Blau/Silber Edelstahllook,
-Logo anbei
- Modernes Team, Flexibilität, Dynamik
- Metallverarbeitendes Unternehmen
- Automobil
-Elektroindustrie

```html
<!DOCTYPE html>
<html lang="de">
<head>
<meta charset="utf-8">
<title>Norvik Metallverarbeitung</title>
<link href="https://fonts.googleapis.com/css2?family=Mulish:wght@300;400;600;700&family=Exo+2:wght@600;700&display=swap" rel="stylesheet">
<style>
:root{
  --navy:#0c3d63;
  --navy-dark:#082c49;
  --ink:#1f2d3a;
  --muted:#6b7683;
  --pale:#f4f8fb;
  --line:#d9e1e8;
  --white:#ffffff;
}
*{box-sizing:border-box;margin:0;padding:0}
html,body{width:1200px;height:3106px;overflow:hidden}
body{font-family:"Mulish",sans-serif;color:var(--ink);background:var(--white);position:relative}
.abs{position:absolute}
.ph{position:absolute}
h2.section-title{font-family:"Exo 2",sans-serif;font-weight:700;color:var(--navy);font-size:30px;letter-spacing:.5px;display:flex;align-items:center;gap:10px}
h2.section-title::before{content:"";width:38px;height:38px;border:4px solid var(--navy);border-radius:50%}
.btn{display:inline-flex;align-items:center;gap:8px;background:var(--navy);color:var(--white);font-size:12.5px;font-weight:600;padding:0 12px;height:36px;border-bottom:3px solid var(--navy-dark)}
.btn svg{width:9px;height:9px}

/* header */
.site-header{top:0;left:0;width:1200px;height:80px;background:var(--white)}
.brand{left:217px;top:18px;display:flex;align-items:center;gap:8px;font-weight:700;font-size:20px;color:var(--navy)}
.brand .dot{width:30px;height:30px;border-radius:50%;background:var(--navy)}
.topbar{right:163px;top:18px;font-size:10px;color:var(--muted);display:flex;gap:12px}
.nav{right:163px;top:40px;display:flex;gap:22px;font-size:11px;font-weight:600;color:var(--ink)}
.nav .active{color:var(--navy);border-bottom:2px solid var(--navy);padding-bottom:6px}

/* hero */
.hero{top:80px;left:0;width:1200px;height:328px;background:linear-gradient(180deg,#1d3550 0%,#0f2237 55%,#2a3a4c 100%);color:var(--white);text-align:center}
.hero .intro{font-size:19px;font-weight:300;margin-top:74px}
.hero h1{font-size:31px;font-weight:700;margin-top:6px}
.hero p{font-size:12.5px;line-height:19px;width:520px;margin:22px auto 0}

/* service cards */
.service{top:464px;width:412px;height:237px}
.service .img{top:0;left:0;width:412px;height:184px}
.service .band{top:184px;left:0;width:412px;height:53px;background:var(--navy);color:var(--white);font-size:12.5px;display:flex;align-items:center;justify-content:center;gap:8px;border-bottom:3px solid var(--navy-dark)}

/* about */
.about{top:766px;left:0;width:1200px;height:363px;background:var(--pale)}
.about .img{left:0;top:0;width:420px;height:363px;background:linear-gradient(135deg,#e9ecef,#b7bfc7 60%,#5d6772)}
.about .text{left:458px;top:56px;width:580px}
.about p{font-size:12px;line-height:19px;color:var(--muted);margin-top:22px}
.values{display:flex;margin-top:20px}
.value{width:195px;text-align:center;font-size:12.5px;font-weight:700;color:var(--navy)}
.value svg{width:46px;height:46px;display:block;margin:0 auto 14px}

/* services */
.services{top:1129px;left:0;width:1200px;height:476px}
.services .img{left:600px;top:0;width:600px;height:476px;background:radial-gradient(circle at 55% 45%,#8d7a3e,#3a3425 45%,#181a1d)}
.cat{top:120px;width:212px}
.cat .icon{width:50px;height:44px;background:#727a82;display:flex;align-items:center;justify-content:center;margin-left:7px}
.cat .label{background:var(--navy);color:var(--white);font-size:12.5px;font-weight:700;height:37px;padding-left:62px;display:flex;align-items:center}
.cat ul{list-style:none;margin-top:12px}
.cat li{font-size:12px;color:var(--muted);line-height:18.8px;display:flex;align-items:center;gap:6px}
.cat li svg{width:9px;height:9px}

/* team */
.team{top:1605px;left:0;width:1200px;height:560px;background:var(--pale)}
.member{top:123px;width:194px;height:319px}
.member .img{left:0;top:0;width:194px;height:205px}
.member .card{left:6px;top:205px;width:182px;height:114px;background:var(--white);border-bottom:3px solid var(--navy);text-align:center}
.member h3{font-size:12px;font-weight:700;color:var(--navy);margin-top:9px}
.member p{font-size:11.5px;line-height:19px;color:var(--muted);margin-top:12px}

/* references */
.refs{top:2165px;left:0;width:1200px;height:347px}
.ref{top:129px;width:254px;height:166px}
.ref .img{left:0;top:0;width:254px;height:127px}
.ref .cap{left:0;top:127px;width:254px;height:39px;background:var(--pale);border-bottom:3px solid var(--navy);font-size:12px;color:var(--muted);display:flex;align-items:center;justify-content:center}
.arrow{top:207px;width:12px;height:12px}

/* gallery */
.gallery{top:2512px;left:0;width:1200px;height:450px}
.tile{width:300px;height:225px}

/* footer */
.site-footer{top:2962px;left:0;width:1200px;height:144px;background:var(--navy);color:var(--white);font-size:11px}
.site-footer .col{top:38px;line-height:19px}
.site-footer strong{font-size:12.5px}
.site-footer .contact div{display:flex;align-items:center;gap:8px}
.site-footer a{color:var(--white)}
.badge{left:895px;top:28px;width:120px;height:80px;border-radius:40px;background:#2f7fbf}
.totop{right:32px;top:114px;width:22px;height:22px;border-radius:50%;background:var(--white)}
</style>
</head>
<body>

<header class="abs site-header">
  <div class="abs brand"><span class="dot"></span>Norvik</div>
  <div class="abs topbar"><span>+49 170 5550182</span><span>info@norvik-metall.de</span></div>
  <nav class="abs nav">
    <span class="active">Startseite</span><span>Über uns</span><span>Leistungen ▾</span><span>Team</span><span>Referenzen</span><span>Galerie</span>
  </nav>
</header>

<section class="abs hero" role="img" aria-label="Laserschneidkopf über einem Metallblech in blauem Licht">
  <div class="intro">Herzlich Willkommen bei</div>
  <h1>Norvik Metallverarbeitung</h1>
  <p>„Made in Germany“ – wir halten unser Qualitätsversprechen!<br>Wir sind Ihr zuverlässigster Partner von der Konstruktion/ Entwicklung bis zum fertig veredelten Endprodukt. Dabei denken wir innovativ, arbeiten kreativ und kombinieren die traditionelle Handwerkskunst mit aktuellem Design.</p>
</section>

<div class="abs service" style="left:175px">
  <div class="ph img" role="img" aria-label="Industrieanlage aus Stahl in Sepiatönen" style="background:linear-gradient(135deg,#a08470,#5e4638)"></div>
  <div class="abs band">Industrie Metallverarbeitung <svg width="9" height="9" viewBox="0 0 10 10"><path d="M5 0l5 5-5 5-1-1 3-3H0V4h7L4 1z" fill="#fff"/></svg></div>
</div>
<div class="abs service" style="left:613px">
  <div class="ph img" role="img" aria-label="Schmiedeeisernes Treppengeländer" style="background:linear-gradient(135deg,#e5e5e5,#8a8a8a 50%,#2b2b2b)"></div>
  <div class="abs band">Home Metallverarbeitung <svg width="9" height="9" viewBox="0 0 10 10"><path d="M5 0l5 5-5 5-1-1 3-3H0V4h7L4 1z" fill="#fff"/></svg></div>
</div>

<section class="abs about">
  <div class="ph img" role="img" aria-label="Laserschneidmaschine in einer Werkhalle"></div>
  <div class="abs text">
    <h2 class="section-title">ÜBER UNS</h2>
    <p>Als inhabergeführtes Unternehmen arbeiten wir seit 2004 als eingetragenes Einzelunternehmen und sind seit 2009 als GmbH im Handelsregister registriert und verfolgen folgende Grundsätzen:</p>
    <div class="values">
      <div class="value"><svg viewBox="0 0 46 46" fill="none" stroke="#0c3d63" stroke-width="2"><rect x="8" y="4" width="32" height="16" rx="2"/><path d="M14 12l2 2 2-2M22 12l2 2 2-2M30 12l2 2 2-2"/><path d="M6 40V26h6v14zM12 28l6-8h3v8h10v10H12"/></svg>Kundenzufriedenheit</div>
      <div class="value"><svg viewBox="0 0 46 46" fill="none" stroke="#0c3d63" stroke-width="2"><circle cx="23" cy="18" r="12"/><circle cx="23" cy="18" r="7"/><path d="M20 18l2 2 4-4M15 28l-5 12 6-2 3 5 4-10M31 28l5 12-6-2-3 5-4-10"/></svg>Hohe Qualität</div>
      <div class="value"><svg viewBox="0 0 46 46" fill="none" stroke="#0c3d63" stroke-width="2"><path d="M13 16a10 10 0 0120 0zM11 16h24"/><circle cx="23" cy="22" r="6"/><path d="M10 42v-6a8 8 0 018-8h10a8 8 0 018 8v6M23 28v14"/></svg>Zufriedene Mitarbeiter</div>
    </div>
    <div style="margin-top:22px"><span class="btn">mehr erfahren <svg viewBox="0 0 10 10"><path d="M5 0l5 5-5 5-1-1 3-3H0V4h7L4 1z" fill="#fff"/></svg></span></div>
  </div>
</section>

<section class="abs services">
  <div class="abs" style="left:120px;top:52px"><h2 class="section-title">Leistungen</h2></div>
  <div class="abs cat" style="left:126px">
    <div class="icon"><svg width="30" height="30" viewBox="0 0 30 30" fill="none" stroke="#fff" stroke-width="1.6"><circle cx="15" cy="15" r="5"/><circle cx="15" cy="15" r="11"/></svg></div>
    <div class="label">Industrie</div>
    <ul>
      <li><svg viewBox="0 0 10 10"><path d="M1 5l3 3 5-6" stroke="#1f2d3a" stroke-width="1.6" fill="none"/></svg>Metallbau</li>
      <li><svg viewBox="0 0 10 10"><path d="M1 5l3 3 5-6" stroke="#1f2d3a" stroke-width="1.6" fill="none"/></svg>Laser</li>
      <li><svg viewBox="0 0 10 10"><path d="M1 5l3 3 5-6" stroke="#1f2d3a" stroke-width="1.6" fill="none"/></svg>Verpackung</li>
      <li><svg viewBox="0 0 10 10"><path d="M1 5l3 3 5-6" stroke="#1f2d3a" stroke-width="1.6" fill="none"/></svg>CAD Konstruktionen</li>
      <li><svg viewBox="0 0 10 10"><path d="M1 5l3 3 5-6" stroke="#1f2d3a" stroke-width="1.6" fill="none"/></svg>Ladungsträger</li>
      <li><svg viewBox="0 0 10 10"><path d="M1 5l3 3 5-6" stroke="#1f2d3a" stroke-width="1.6" fill="none"/></svg>Lackiergestelle/ Skids</li>
      <li><svg viewBox="0 0 10 10"><path d="M1 5l3 3 5-6" stroke="#1f2d3a" stroke-width="1.6" fill="none"/></svg>uvm…</li>
    </ul>
  </div>
  <div class="abs cat" style="left:351px">
    <div class="icon"><svg width="30" height="30" viewBox="0 0 30 30" fill="none" stroke="#fff" stroke-width="1.6"><path d="M3 15L15 4l12 11M7 12v14h16V12M12 26v-8h6v8"/></svg></div>
    <div class="label">Home</div>
    <ul>
      <li><svg viewBox="0 0 10 10"><path d="M1 5l3 3 5-6" stroke="#1f2d3a" stroke-width="1.6" fill="none"/></svg>Treppengeländer</li>
      <li><svg viewBox="0 0 10 10"><path d="M1 5l3 3 5-6" stroke="#1f2d3a" stroke-width="1.6" fill="none"/></svg>Balkone</li>
      <li><svg viewBox="0 0 10 10"><path d="M1 5l3 3 5-6" stroke="#1f2d3a" stroke-width="1.6" fill="none"/></svg>Handläufe</li>
      <li><svg viewBox="0 0 10 10"><path d="M1 5l3 3 5-6" stroke="#1f2d3a" stroke-width="1.6" fill="none"/></svg>Feuersäulen</li>
      <li><svg viewBox="0 0 10 10"><path d="M1 5l3 3 5-6" stroke="#1f2d3a" stroke-width="1.6" fill="none"/></svg>Grill</li>
      <li><svg viewBox="0 0 10 10"><path d="M1 5l3 3 5-6" stroke="#1f2d3a" stroke-width="1.6" fill="none"/></svg>Tische</li>
      <li><svg viewBox="0 0 10 10"><path d="M1 5l3 3 5-6" stroke="#1f2d3a" stroke-width="1.6" fill="none"/></svg>Sichtschutz für den Garten</li>
      <li><svg viewBox="0 0 10 10"><path d="M1 5l3 3 5-6" stroke="#1f2d3a" stroke-width="1.6" fill="none"/></svg>uvm…</li>
    </ul>
  </div>
  <div class="abs" style="left:120px;top:383px"><span class="btn">mehr erfahren <svg viewBox="0 0 10 10"><path d="M5 0l5 5-5 5-1-1 3-3H0V4h7L4 1z" fill="#fff"/></svg></span></div>
  <div class="ph img" role="img" aria-label="Zwei Druckmanometer an einem Schweißgasregler"></div>
</section>

<section class="abs team">
  <div class="abs" style="left:0;width:1200px;top:55px;display:flex;justify-content:center"><h2 class="section-title">Team</h2></div>
  <div class="abs member" style="left:175px">
    <div class="ph img" role="img" aria-label="Porträt eines Mitarbeiters im Anzug" style="background:linear-gradient(180deg,#2f5577,#1c3a57)"></div>
    <div class="abs card"><h3>Max Mustermann</h3><p>Muster kurze Beschreibung<br>Lorem ipsum dolor sit amet,<br>consectetur adipiscing elit.</p></div>
  </div>
  <div class="abs member" style="left:394px">
    <div class="ph img" role="img" aria-label="Porträt einer Mitarbeiterin" style="background:linear-gradient(180deg,#2f5577,#1c3a57)"></div>
    <div class="abs card"><h3>Sarah Musterfrau</h3><p>Muster kurze Beschreibung<br>Lorem ipsum dolor sit amet,<br>consectetur adipiscing elit.</p></div>
  </div>
  <div class="abs member" style="left:613px">
    <div class="ph img" role="img" aria-label="Porträt eines Mitarbeiters mit Schutzhelm" style="background:linear-gradient(180deg,#3a6185,#1c3a57)"></div>
    <div class="abs card"><h3>Max Mustermann</h3><p>Muster kurze Beschreibung<br>Lorem ipsum dolor sit amet,<br>consectetur adipiscing elit.</p></div>
  </div>
  <div class="abs member" style="left:831px">
    <div class="ph img" role="img" aria-label="Porträt eines Mitarbeiters mit Warnweste" style="background:linear-gradient(180deg,#3a6185,#1c3a57)"></div>
    <div class="abs card"><h3>Max Mustermann</h3><p>Muster kurze Beschreibung<br>Lorem ipsum dolor sit amet,<br>consectetur adipiscing elit.</p></div>
  </div>
  <div class="abs" style="left:542px;top:466px"><span class="btn">mehr erfahren <svg viewBox="0 0 10 10"><path d="M5 0l5 5-5 5-1-1 3-3H0V4h7L4 1z" fill="#fff"/></svg></span></div>
</section>

<section class="abs refs">
  <div class="abs" style="left:0;width:1200px;top:56px;display:flex;justify-content:center"><h2 class="section-title">Referenzen</h2></div>
  <svg class="abs arrow" style="left:171px" viewBox="0 0 12 12"><path d="M8 1L3 6l5 5" stroke="#0c3d63" stroke-width="2" fill="none"/></svg>
  <div class="abs ref" style="left:187px"><div class="ph img" role="img" aria-label="Stahlgestell in einer Fertigungshalle" style="background:linear-gradient(135deg,#a08470,#5e4638)"></div><div class="abs cap">Muster Referenz 3</div></div>
  <div class="abs ref" style="left:473px"><div class="ph img" role="img" aria-label="Gitterrahmen aus Edelstahl" style="background:linear-gradient(135deg,#e6e9ec,#a9b1b9)"></div><div class="abs cap">Muster Referenz 4</div></div>
  <div class="abs ref" style="left:757px"><div class="ph img" role="img" aria-label="CAD-Modell eines gebogenen Bauteils" style="background:linear-gradient(135deg,#1e2b55,#3b4f86)"></div><div class="abs cap">Muster Referenz 5</div></div>
  <svg class="abs arrow" style="left:1018px" viewBox="0 0 12 12"><path d="M4 1l5 5-5 5" stroke="#0c3d63" stroke-width="2" fill="none"/></svg>
</section>

<section class="abs gallery">
  <div class="abs tile" style="left:0;top:0;background:var(--white);display:flex;align-items:center;padding-left:95px"><h2 class="section-title">Galerie</h2></div>
  <div class="ph tile" style="left:300px;top:0;background:radial-gradient(circle at 50% 55%,#f0a040,#9a3b10 50%,#2a1408)" role="img" aria-label="Funkenflug beim Laserschneiden"></div>
  <div class="ph tile" style="left:600px;top:0;background:linear-gradient(135deg,#c9ccd0,#8a8f95 45%,#e07a20)" role="img" aria-label="Förderanlage mit orangefarbenen Rollen"></div>
  <div class="ph tile" style="left:900px;top:0;background:linear-gradient(135deg,#3d3834,#1c2a2a)" role="img" aria-label="Metallrohr im Außenbereich"></div>
  <div class="ph tile" style="left:0;top:225px;background:linear-gradient(180deg,#7a6048,#6a6e72)" role="img" aria-label="Holzdachstuhl mit Stahlrost"></div>
  <div class="ph tile" style="left:300px;top:225px;background:linear-gradient(135deg,#e5e6e4,#a9a9a2)" role="img" aria-label="Lagerhalle aus Stahlträgern"></div>
  <div class="ph tile" style="left:600px;top:225px;background:linear-gradient(135deg,#eef2f6,#9fb4c8)" role="img" aria-label="Glasdach mit Stahlkonstruktion"></div>
  <div class="abs tile" style="left:900px;top:225px;background:var(--navy)">
    <span class="abs" style="left:111px;top:92px;background:var(--white);color:var(--navy);font-size:12px;height:34px;padding:0 12px;display:flex;align-items:center;gap:8px">Galerie <svg width="9" height="9" viewBox="0 0 10 10"><path d="M5 0l5 5-5 5-1-1 3-3H0V4h7L4 1z" fill="#0c3d63"/></svg></span>
  </div>
</section>

<footer class="abs site-footer">
  <div class="abs col" style="left:175px"><strong>Norvik Metallverarbeitung</strong><br>Werkstraße 21<br>77933 Lahrfeld</div>
  <div class="abs col contact" style="left:404px;top:30px">
    <div><svg width="10" height="10" viewBox="0 0 10 10"><path d="M2 0l2 2-1 2 3 3 2-1 2 2-2 2C4 10 0 6 0 2z" fill="#fff"/></svg>+49 761 5550140</div>
    <div><svg width="10" height="10" viewBox="0 0 10 10"><rect x="2.5" y="0" width="5" height="10" rx="1" fill="#fff"/></svg>+49 176 5550193</div>
    <div><svg width="10" height="10" viewBox="0 0 10 10"><rect x="0" y="3" width="10" height="6" fill="#fff"/><rect x="2" y="0" width="6" height="3" fill="#fff"/></svg>+49 761 5550141</div>
    <div><svg width="10" height="10" viewBox="0 0 10 10"><rect x="0" y="1.5" width="10" height="7" fill="#fff"/></svg>info@norvik-metall.de</div>
  </div>
  <div class="abs col" style="left:633px;top:49px"><a href="#">Datenschutz</a><br><a href="#">Impressum</a></div>
  <div class="abs badge" role="img" aria-label="Zertifizierungssiegel"></div>
  <div class="abs totop"></div>
</footer>

</body>
</html>
```